Aerial Imaging and photgraphy business card

Design a business card with eye catching aerial photo of country side / landscape with a drone in the foreground.
Also contact details.

Target Market(s)

Aerial Imaging photography

Industry/Entity Type

Advertising

Contact Information for Business Card

Rowland
0412965203
Website http://www.skywardvistaphoto.com.au/
email address : skywardvistaphoto.com.au

Colors
e8f1ca
cadf82
9bcb3c
33a6d7
85cae6
cee9f5

Requirements
Must have
• High res photo
• Korvane drone in the foreground Either T4200 and korvane Glidewing or both
Nice to have
• high resolution landscape country photo on the front of the card with a Korvane T4200 drone in the foreground.

```html
<!DOCTYPE html>
<html lang="en">
<head>
<meta charset="utf-8">
<title>Skyward Vista Photo – Business Card</title>
<link rel="stylesheet" href="https://fonts.googleapis.com/css2?family=Open+Sans:wght@400;600;700&display=swap">
<style>
  :root {
    --page-bg: #e9e6e3;
    --field-green-dark: #5a9448;
    --field-green-light: #7cb062;
    --panel-light: #f4eeeb;
    --text-white: #ffffff;
    --brand-dark: #3b3e42;
    --brand-accent: #9bcb3c;
    --photo-tone-a: #6fa35a;
    --photo-tone-b: #4d5b4c;
  }
  * { margin: 0; padding: 0; box-sizing: border-box; }
  html, body {
    width: 1200px; height: 900px; overflow: hidden;
    background: var(--page-bg);
    font-family: "Open Sans", Arial, sans-serif;
  }
  .business-card {
    position: absolute;
    left: 120px; top: 155px;
    width: 960px; height: 590px;
    overflow: hidden;
    background: var(--panel-light);
    box-shadow: 0 12px 36px rgba(0,0,0,0.18);
  }
  .field-backdrop {
    position: absolute; inset: 0;
    background: linear-gradient(160deg, var(--field-green-light) 0%, var(--field-green-dark) 100%);
    clip-path: polygon(0 0, 420px 0, 600px 590px, 0 590px);
  }
  .drone-photo {
    position: absolute;
    left: 35px; top: 56px;
    width: 345px; height: 205px;
    border-radius: 8px;
    background: radial-gradient(ellipse at 50% 45%, var(--photo-tone-b) 0%, var(--photo-tone-a) 70%, transparent 100%);
    opacity: 0.85;
  }
  .card-holder {
    position: absolute; left: 35px; top: 330px;
    color: var(--text-white);
  }
  .holder-name {
    font-size: 30px; font-weight: 600; letter-spacing: 0.5px;
    text-transform: uppercase; line-height: 1.1;
  }
  .holder-role { font-size: 22px; font-weight: 400; margin-top: 4px; }
  .contact-list {
    position: absolute; left: 35px; top: 462px;
    list-style: none; color: var(--text-white);
    font-size: 23px; line-height: 34px;
  }
  .contact-list li { display: flex; align-items: center; gap: 10px; }
  .contact-list svg { width: 20px; height: 20px; fill: var(--text-white); flex: none; }
  .brand-mark {
    position: absolute; left: 470px; top: 0; width: 490px; height: 590px;
    display: flex; flex-direction: column; align-items: center; justify-content: center; gap: 26px;
  }
  .brand-dot {
    width: 110px; height: 110px; border-radius: 50%;
    background: var(--brand-accent);
  }
  .brand-name {
    font-size: 50px; font-weight: 700; color: var(--brand-dark);
    text-align: center; line-height: 1.1; text-transform: uppercase;
  }
</style>
</head>
<body>
  <main class="business-card">
    <div class="field-backdrop" role="img" aria-label="Aerial photo of green countryside fields"></div>
    <div class="drone-photo" role="img" aria-label="Photo of a camera drone in flight"></div>

    <div class="card-holder">
      <p class="holder-name">Rowland Pike</p>
      <p class="holder-role">General Manager</p>
    </div>

    <ul class="contact-list">
      <li>
        <svg viewBox="0 0 24 24" aria-hidden="true"><path d="M6.6 10.8a15.1 15.1 0 0 0 6.6 6.6l2.2-2.2c.3-.3.7-.4 1-.2 1.1.4 2.3.6 3.6.6.6 0 1 .4 1 1V20c0 .6-.4 1-1 1A17 17 0 0 1 3 4c0-.6.4-1 1-1h3.5c.6 0 1 .4 1 1 0 1.3.2 2.5.6 3.6.1.3 0 .7-.2 1z"/></svg>
        (403) 555-0182
      </li>
      <li>
        <svg viewBox="0 0 24 24" aria-hidden="true"><path d="M2 5h20v14H2z M2 5l10 8 10-8" fill="none" stroke="#fff" stroke-width="2"/><path d="M3 6l9 7 9-7v12H3z"/></svg>
        info@skywardvistaphoto.com.au
      </li>
      <li>
        <svg viewBox="0 0 24 24" aria-hidden="true"><path d="M12 2a10 10 0 1 0 0 20 10 10 0 0 0 0-20zm-1 17.9A8 8 0 0 1 4.1 10L9 15v1a2 2 0 0 0 2 2zm6.9-2.5A2 2 0 0 0 16 16h-1v-3a1 1 0 0 0-1-1H8v-2h2a1 1 0 0 0 1-1V7h2a2 2 0 0 0 2-2v-.4a8 8 0 0 1 2.9 12.8z"/></svg>
        www.skywardvistaphoto.com.au
      </li>
    </ul>

    <div class="brand-mark">
      <span class="brand-dot" aria-hidden="true"></span>
      <p class="brand-name">Skyward Vista<br>Photo</p>
    </div>
  </main>
</body>
</html>
```